Two Separate Canvas Posters 54"width x 36" Height

I need two (2) posters designed for a new restaurant concept called: Lumara Fresh Pita Grill.
Both posters will be printed on Canvas and placed into our new restaurants dining area.
I want this to look hip and cool.
I want so see red colors and earth tones. Please see attached for some ideas that I have.
The final design should communicate that you really gotta have this product and that this is a fun and casual place for a quick bite on the go.
Poster 1 message: gotta Eatta pita!
Size: 54"width x 36" high
Idea: Please see attached for design ideas and colors that I would like to see. If you can come up with any better idea, I would love to see this.
Poster 2 message: Power to the Pita
Size: 54"width x 36" height
Idea: Please see attached for design idea and colors that I want to see.
Industry/Entity Type
Restaurant
Look and feel
Each slider illustrates characteristics of the customer's brand and the style your logo design should communicate.

```html
<!DOCTYPE html>
<html lang="en">
<head>
<meta charset="utf-8">
<title>Power to the Pita — Lumara Fresh Pita Grill poster</title>
<link href="https://fonts.googleapis.com/css2?family=Archivo+Black&display=swap" rel="stylesheet">
<style>
  :root {
    --poster-red: #8a1a10;
    --poster-red-deep: #6a140c;
    --ray-rust: #9a3d14;
    --headline-yellow: #c8ae1e;
    --accent-orange: #d9812b;
  }
  html, body {
    margin: 0;
    padding: 0;
    width: 1200px;
    height: 800px;
    overflow: hidden;
    background: var(--poster-red);
  }
  .poster {
    display: block;
    width: 1200px;
    height: 800px;
  }
  .headline {
    font-family: "Archivo Black", "Arial Black", sans-serif;
    fill: var(--headline-yellow);
  }
  .headline--connector { fill: var(--accent-orange); }
</style>
</head>
<body>
<svg class="poster" viewBox="0 0 1200 800" xmlns="http://www.w3.org/2000/svg">
  <defs>
    <radialGradient id="backdrop-tone" cx="40%" cy="62%" r="75%">
      <stop offset="0%" stop-color="#9a3d14"/>
      <stop offset="45%" stop-color="#8e2a12"/>
      <stop offset="80%" stop-color="#8a1a10"/>
      <stop offset="100%" stop-color="#6a140c"/>
    </radialGradient>
  </defs>

  <rect class="poster__backdrop" x="0" y="0" width="1200" height="800"
        fill="url(#backdrop-tone)" role="img"
        aria-label="Red and rust sunburst rays radiating from behind the headline, with a worn grunge texture"/>

  <g class="headline-group">
    <text class="headline headline--power" x="15" y="353" font-size="408"
          textLength="1163" lengthAdjust="spacingAndGlyphs">POWER</text>
    <text class="headline headline--connector" font-size="74"
          transform="translate(68,717) rotate(-90)" x="0" y="0"
          textLength="334" lengthAdjust="spacingAndGlyphs">TO THE</text>
    <text class="headline headline--pita" x="262" y="717" font-size="484"
          textLength="916" lengthAdjust="spacingAndGlyphs">PITA</text>
  </g>
</svg>
</body>
</html>
```